International Marketing Company - Web Design Project

vRelay is a well-funded start up in London developing an Online Marketing Platform for small businesses in Europe.

We require a large number of high quality business web designs for our business website builder. Our business websites are completely integrated into our Online Marketing systems and therefore it is important for designers to comply with our Design Guidelines.

This initial contest is a trial for us to open up the design process to top designers for the Builders vertical (e.g. Builders, Electricians, Plumbers, Flooring, etc.). We have implemented a base html structure and design and included them in the files.

Use your creativity to design new and fresh designs based on the included elements (e.g. testimonials, business description, etc).

We will award the stated prize money for the top three designs.

Any designers that submit designs we feel are of a high enough quality but do not make the top 3 could still be compensated and WILL be invited to participate in our next vertical competition.

Therefore, we encourage designers to submit as many designs as possible as we may award up to 25 designs.

Submissions will be reviewed daily and feedback provided where possible.

Designers who can also code will have the options to implement their designs for an additional fee.

Good luck!
Updates

There has been a mistake made in regard to the prize. Pixel Harbor should have it fixed soon.

1st place = £350
2nd place = £250
3rd Place = £150

Thanks,
Morris
25/11/2011

UPDATE:

1st place will win £350
2nd place will win £250
3rd place will win £150

Everything else is as to the specification.

Thanks
Morris

Target Market(s)

Builders, Electricians, Plumbers, Tradesman, Small construction companies

Industry/Entity Type

Business

Requirements
Must have
• Totally new designs based around the elements we want to show on each page.

We are looking for something different to the design we already have. But you can use that as a starting point.

Use the included files to see what is required for each page. Here is a brief outline:

Homepage - Testimonials, News, Business Description, Latest Projects and Call to action

About-Us - Team Summary, About the Business and a call to action

Projects Page - Project Details (Oage Title and description), Each project needs a title, content and 2 images.

Testimonials Page - The testifiers name and their comment

Contacts Page - Terrafind Map, Company address, business hours, contact form and a call to action.

Please submit final designs in Photoshop or Fireworks format.

Each page has a set of elements. These element must feature in the design of that page. See supporting documents for page details.

All elements must be included in your design. Please do not add any extra element.

Professional look and feel
Nice to have
• Design variations:
Full width designs
Boxed Designs
With AND without carousels
OR static images
Good use of stock images.

Creative use of the elements, dont be restricted/influenced by the default design we have already

Designs based on the 960 grid

```html
<!DOCTYPE html>
<html lang="en">
<head>
<meta charset="utf-8">
<title>Harrow Builders – Home</title>
<link href="https://fonts.googleapis.com/css2?family=Arimo:ital,wght@0,400;0,700;1,400&family=Oswald:wght@500;700&display=swap" rel="stylesheet">
<style>
:root{
  --ink:#333;
  --muted:#555;
  --soft:#8a8a8a;
  --blue:#1e90e8;
  --dark:#222;
  --paper:#f7f7f7;
  --band:#efefef;
  --line:#cfcfcf;
  --white:#fff;
}
*{box-sizing:border-box;margin:0;padding:0}
html,body{width:903px;height:1200px;overflow:hidden}
body{position:relative;background:var(--paper);font-family:"Arimo",Arial,sans-serif;color:var(--ink);font-size:9px;line-height:1.4}
.abs{position:absolute}
.blue{color:var(--blue)}
.dark-bar{left:0;width:903px;height:22px;background:var(--dark)}
.topbar{top:22px;left:0;width:903px;height:40px;background:#f2f2f2;border-bottom:1px dashed var(--line)}
.mail{left:120px;top:9px;display:flex;align-items:center;gap:6px;color:var(--soft);font-size:10px}
.mail-icon{width:22px;height:22px;border-radius:50%;background:#bdbdbd;display:flex;align-items:center;justify-content:center}
.phone{right:120px;top:9px;display:flex;align-items:center;gap:8px;font-size:18px;color:var(--dark)}
.brand{left:120px;top:80px}
.brand-name{font-weight:700;font-size:30px;line-height:1;color:var(--dark)}
.brand-tag{font-size:10px;color:#555;margin-top:5px;letter-spacing:.5px}
.nav{right:120px;top:93px;display:flex;font-size:10px}
.nav a{color:var(--ink);text-decoration:none;padding:0 12px;border-left:1px dashed #c8c8c8;line-height:22px}
.nav a:first-child{border-left:0;color:var(--blue)}
.nav a:last-child{padding-right:0}
.slider{left:113px;top:148px;width:677px;height:290px;background:#f0f0f0}
.slide-photo{left:0;top:0;width:367px;height:290px;background:linear-gradient(135deg,#5a4632,#a47b4f 45%,#c9a070 60%,#6b5440)}
.strip1{left:367px;top:0;width:27px;height:290px;background:#777}
.strip2{left:394px;top:0;width:54px;height:290px;background:linear-gradient(#8a8a8a,#a3a3a3)}
.caption{left:40px;top:66px;color:#fff;font-size:11px;line-height:14px}
.caption span{display:block}
.caption span+span{padding-left:56px}
.dots{left:26px;top:247px;width:76px;height:22px;background:#333;border-radius:3px;display:flex;gap:5px;align-items:center;justify-content:center}
.dots i{width:8px;height:8px;border-radius:50%;background:#bbb}
.dots i:first-child{background:var(--blue)}
.arrow{top:114px;width:30px;height:52px;background:#fff;opacity:.9}
.arrow.prev{left:0;border-radius:0 26px 26px 0}
.arrow.next{right:0;border-radius:26px 0 0 26px;background:#e6e6e6}
.slide-text{left:467px;top:52px;width:200px}
.slide-text h2{font-weight:400;font-size:24px;color:#444;letter-spacing:-.5px;line-height:1}
.slide-text p{color:var(--blue);font-size:10px;margin-top:12px;line-height:13px}
.slide-text ul{list-style:none;margin-top:12px;padding-left:28px}
.slide-text li{position:relative;padding-left:24px;font-size:9px;color:#444;line-height:21px}
.slide-text li::before{content:"";position:absolute;left:0;top:6px;width:8px;height:8px;border-radius:50%;background:var(--blue)}
.welcome{top:466px;left:0;width:903px;height:212px;background:var(--band);border-top:1px dashed var(--line);border-bottom:1px dashed var(--line)}
.welcome-copy{left:120px;top:20px;width:438px}
.section-title{font-size:15px;font-weight:400;color:var(--ink)}
.welcome-copy p{font-size:8.5px;color:var(--muted);text-align:justify;line-height:12.8px;margin-top:6px}
.welcome-copy p+p{margin-top:12px}
.btn{display:inline-block;background:linear-gradient(#fff,#e6e6e6);border:1px solid #ccc;border-radius:3px;box-shadow:0 1px 2px rgba(0,0,0,.2);font-weight:700;font-size:9px;color:#333;padding:5px 7px}
.welcome .btn{left:498px;top:170px}
.cta{left:584px;top:67px;width:186px;height:87px;border-radius:5px;background:linear-gradient(#f4f4f4,#cfcfcf);border:1px solid #bbb;box-shadow:0 6px 8px rgba(0,0,0,.15)}
.cta svg{left:8px;top:14px}
.cta-divider{left:68px;top:20px;width:1px;height:50px;background:#bbb}
.cta-title{left:80px;top:20px;font-family:"Oswald",sans-serif;font-weight:700;font-size:20px;color:#444;line-height:1}
.cta-sub{left:84px;top:45px;font-size:11px;color:#888}
.col-title{display:flex;align-items:center;gap:6px;font-size:15px;font-weight:400}
.col-title::before{content:"";width:8px;height:20px;background:#cfcfcf}
.quote{width:200px;height:62px;background:#efefef;border:1px solid #e2e2e2;padding:10px 5px;font-style:italic;font-size:8px;color:#555;line-height:10px;text-align:justify}
.quote::after{content:"";position:absolute;left:8px;bottom:-9px;border:4px solid transparent;border-top:5px solid #e6e6e6}
.who{font-size:8px;color:#333}
.news-item{width:188px;font-size:8px;color:#444;line-height:10px;text-align:justify}
.news-sep{width:196px;border-top:1px dashed #cfcfcf}
.project-thumb{left:573px;width:63px;height:64px;border:2px solid #ddd}
.project-info{left:646px;font-size:8px;color:#444;line-height:10px;width:125px}
.project-info .name{color:var(--blue);font-size:9.5px;margin-bottom:10px}
.project-info .loc{margin-top:10px}
.proj-sep{left:573px;width:196px;border-top:1px dashed #cfcfcf}
.footer{top:1138px;left:0;width:903px;height:40px;border-top:1px dashed var(--line)}
.foot-nav{left:117px;top:20px;font-size:7px;color:#555}
.foot-nav .cur{color:var(--blue)}
.copyright{left:432px;top:18px;font-size:8.5px;color:#777}
.social{left:659px;top:10px;display:flex;gap:4px}
.social i{width:22px;height:22px;border-radius:50%;background:#aaa}
</style>
</head>
<body>
<div class="abs dark-bar" style="top:0"></div>

<header>
  <div class="abs topbar">
    <div class="abs mail">
      <span class="mail-icon"><svg width="11" height="8" viewBox="0 0 11 8"><rect x=".5" y=".5" width="10" height="7" fill="#fff" stroke="#999"/><path d="M.5 .5 5.5 4.5 10.5 .5" fill="none" stroke="#999"/></svg></span>
      hello@harrowbuilders.co.uk
    </div>
    <div class="abs phone">
      <svg width="16" height="16" viewBox="0 0 16 16"><rect width="16" height="16" rx="2" fill="#777"/><path d="M5 3c-1 1-1 3 0 5s3 4 5 5c1 0 2 0 2-1l-2-2-1 1c-1-1-2-2-3-4l1-1z" fill="#fff"/></svg>
      020 7946 0321
    </div>
  </div>

  <div class="abs brand">
    <div class="brand-name">HARROW BUILDERS</div>
    <div class="brand-tag">Quick &nbsp; Solid &nbsp; Quality</div>
  </div>

  <nav class="abs nav">
    <a href="#">HOME</a><a href="#">ABOUT US</a><a href="#">TESTIMONIAL</a><a href="#">PORTFOLIO</a><a href="#">CONTACT</a>
  </nav>
</header>

<section class="abs slider">
  <div class="abs slide-photo" role="img" aria-label="Carpenter's hands marking a timber board with a pencil and tape measure"></div>
  <div class="abs strip1"></div>
  <div class="abs strip2"></div>
  <div class="abs caption"><span>I am a friendly, handyman who has</span><span>built a team of excellent tradesmen</span></div>
  <div class="abs dots"><i></i><i></i><i></i><i></i></div>
  <div class="abs arrow prev"><svg width="30" height="52" viewBox="0 0 30 52"><path d="M17 16 8 26l9 10" fill="none" stroke="#ccc" stroke-width="4"/></svg></div>
  <div class="abs arrow next"><svg width="30" height="52" viewBox="0 0 30 52"><path d="M13 16l9 10-9 10" fill="none" stroke="#fff" stroke-width="4"/></svg></div>
  <div class="abs slide-text">
    <h2>HARROW BUILDERS</h2>
    <p>My builders in Crawley have years<br>of experience in</p>
    <ul>
      <li>Kitchen renovation,</li>
      <li>Bathroom renovation,</li>
      <li>Roofing and plumbing,</li>
      <li>Loft conversions and</li>
      <li>House restoration.</li>
    </ul>
  </div>
</section>

<section class="abs welcome">
  <div class="abs welcome-copy">
    <h1 class="section-title">Welcome to <span class="blue">HARROW BUILDERS</span></h1>
    <p>I am an experienced builder in Crawley, Harrow Construction have been based in Crawley for over 10 years. My team and I are proven, reliable builders based in Crawley. We've come across a lot in our time, so don't hesitate to get in touch about any building job in Crawley.</p>
    <p>I am a friendly, handyman who has built a team of excellent tradesmen based in Crawley. My builders in Crawley have years of experience in kitchen renovation, bathroom renovation, roofing and plumbing, loft conversions and house restoration.</p>
    <p>Call Harrow Construction on 0199 555 0142 now to discuss how we can help you. My quotes are always FREE with no obligation.</p>
  </div>
  <a class="abs btn">Read More</a>
  <div class="abs cta">
    <svg class="abs" width="50" height="48" viewBox="0 0 50 48"><circle cx="25" cy="14" r="10" fill="#444"/><path d="M3 48c0-14 10-20 22-20s22 6 22 20z" fill="#444"/></svg>
    <div class="abs cta-divider"></div>
    <div class="abs cta-title">Contact Us</div>
    <div class="abs cta-sub">For a Quote Now</div>
  </div>
</section>

<section class="testimonials">
  <h2 class="abs col-title" style="left:120px;top:716px">Customer <span class="blue">SAY</span></h2>
  <blockquote class="abs quote" style="left:120px;top:752px">"Harrow Construction are the best builders in Crawley. They are experts in all areas of house building and I am extremely satisfied with my new loft conversion."</blockquote>
  <div class="abs who" style="left:123px;top:829px"><span class="blue">Mr. Halvorsen</span> - Director</div>
  <blockquote class="abs quote" style="left:120px;top:858px">"Harrow Construction are the best builders in Crawley. They are experts in all areas of house building and I am extremely satisfied with my new loft conversion."</blockquote>
  <div class="abs who" style="left:123px;top:935px"><span class="blue">Mr. Halvorsen</span> - Director</div>
  <blockquote class="abs quote" style="left:120px;top:970px">"Harrow Construction are the best builders in Crawley. They are experts in all areas of house building and I am extremely satisfied with my new loft conversion."</blockquote>
  <div class="abs who" style="left:123px;top:1047px"><span class="blue">Mr. Halvorsen</span> - Director</div>
  <a class="abs btn" style="left:258px;top:1069px">Read More</a>
</section>

<section class="news">
  <h2 class="abs col-title" style="left:346px;top:716px">Latest <span class="blue">NEWS</span></h2>
  <p class="abs news-item" style="left:353px;top:757px">Harrow Construction have just finished another fine job in Crawley.</p>
  <a class="abs btn" style="left:480px;top:785px">Read More</a>
  <div class="abs news-sep" style="left:350px;top:818px"></div>
  <p class="abs news-item" style="left:353px;top:830px">Timber frames seem to be all the rage in London. Using the latest in wood tech!</p>
  <a class="abs btn" style="left:480px;top:857px">Read More</a>
  <div class="abs news-sep" style="left:350px;top:890px"></div>
  <p class="abs news-item" style="left:353px;top:903px">Just started a 12th century flat conversion. Lots of great finds!</p>
  <a class="abs btn" style="left:480px;top:930px">Read More</a>
  <div class="abs news-sep" style="left:350px;top:966px"></div>
  <p class="abs news-item" style="left:353px;top:979px">Harrow Construction have just finished another fine job in Crawley.</p>
  <a class="abs btn" style="left:480px;top:1006px">Read More</a>
</section>

<section class="projects">
  <h2 class="abs col-title" style="left:573px;top:716px">Latest <span class="blue">PROJECT</span></h2>

  <div class="abs project-thumb" style="top:758px;background:linear-gradient(#8a7262,#2b2522)" role="img" aria-label="Restored living room with dark leather sofas"></div>
  <div class="abs project-info" style="top:759px"><div class="name">PROJECT 1</div>House restoration in Crawley.<div class="loc">Location : London, England.<br>Author : <span class="blue">Daniel Ashcombe</span></div></div>
  <div class="abs proj-sep" style="top:831px"></div>

  <div class="abs project-thumb" style="top:842px;background:linear-gradient(#c99a63,#efe4d4)" role="img" aria-label="Warmly lit dining room in a loft conversion"></div>
  <div class="abs project-info" style="top:843px"><div class="name">PROJECT 2</div>Loft Conversion near Crawley<div class="loc">Location : London, England.<br>Author : <span class="blue">Daniel Ashcombe</span></div></div>
  <div class="abs proj-sep" style="top:920px"></div>

  <div class="abs project-thumb" style="top:930px;background:linear-gradient(90deg,#dfe6e4,#c9a57a)" role="img" aria-label="Freshly painted kitchen with wooden cabinets"></div>
  <div class="abs project-info" style="top:931px"><div class="name">PROJECT 3</div>Home painting &amp; Decorating in Crawley<div class="loc">Location : London, England.<br>Author : <span class="blue">Daniel Ashcombe</span></div></div>
  <div class="abs proj-sep" style="top:1008px"></div>

  <div class="abs project-thumb" style="top:1018px;background:linear-gradient(90deg,#9c9a94,#ecebe6)" role="img" aria-label="Bright hallway in a house extension"></div>
  <div class="abs project-info" style="top:1020px"><div class="name">PROJECT 4</div>Beautiful house extension<br>in Crawley<div class="loc">Location : London, England.<br>Author : <span class="blue">Daniel Ashcombe</span></div></div>
</section>

<footer class="abs footer">
  <div class="abs foot-nav"><span class="cur">HOME</span> &nbsp;/&nbsp; ABOUT US &nbsp;/&nbsp; TESTIMONIAL &nbsp;/&nbsp; PORTFOLIO &nbsp;/&nbsp; CONTACT</div>
  <div class="abs copyright">Copyright © 2011 Managed by: vrelay.com &nbsp;&nbsp;| &nbsp;&nbsp;<span class="blue">Admin</span></div>
  <div class="abs social" aria-label="Social links"><i></i><i></i><i></i><i></i><i></i></div>
</footer>
<div class="abs dark-bar" style="top:1178px"></div>
</body>
</html>
```